SkyvornQ Business Cards and Stationary Design

Need a design for our business cards and stationary. I want to carry on the theme of the logo. I want the business cards to have a design on the back. I would like the business cards and the stationary to carry the same theme, design scheme, and branding

Target Market(s)

Airlines and Maintenance Facilities

Industry/Entity Type

Aviation

Contact Information for Business Card

Name
Position Title
Address: 4827 Trellis Hollow Road, Fort Pierce, Florida, 34951
Office Number
Mobile Number
Email
Website

Font styles to use
Serif
Sans Serif

Colors

Designer to choose colors to be used in the design.

```html
<!DOCTYPE html>
<html lang="en">
<head>
<meta charset="utf-8">
<title>SkyvornQ Business Card</title>
<link rel="stylesheet" href="https://fonts.googleapis.com/css2?family=Arimo:wght@400;700&family=Open+Sans:wght@400&display=swap">
<style>
  :root {
    --backdrop: #8a5a34;
    --kraft-light: #d3aa80;
    --kraft-mid: #c59a6c;
    --kraft-dark: #b5895c;
    --ink: #141210;
    --card-shadow: rgba(0, 0, 0, 0.35);
  }
  * { margin: 0; padding: 0; box-sizing: border-box; }
  html, body {
    width: 1200px;
    height: 900px;
    overflow: hidden;
    background: var(--backdrop);
  }
  .canvas {
    position: relative;
    width: 1200px;
    height: 900px;
  }
  .card {
    position: absolute;
    background: linear-gradient(160deg, var(--kraft-light) 0%, var(--kraft-mid) 45%, var(--kraft-dark) 100%);
    box-shadow: 3px 4px 8px var(--card-shadow);
    color: var(--ink);
    text-align: center;
  }
  .card--front { left: 330px; top: 90px; width: 555px; height: 343px; }
  .card--back  { left: 330px; top: 470px; width: 558px; height: 342px; }

  .person-name {
    position: absolute;
    top: 150px; left: 0; right: 0;
    font-family: "Arimo", Arial, sans-serif;
    font-weight: 700;
    font-size: 22px;
    letter-spacing: 0.5px;
    line-height: 1;
    transform: translateY(-90px);
  }
  .person-title {
    position: absolute;
    top: 86px; left: 0; right: 0;
    font-family: "Arimo", Arial, sans-serif;
    font-size: 16px;
    line-height: 1;
  }
  .divider {
    position: absolute;
    left: 180px;
    width: 195px;
    height: 1px;
    background: var(--ink);
  }
  .divider--upper { top: 116px; }
  .divider--lower { top: 222px; }
  .contact-list {
    position: absolute;
    top: 129px; left: 0; right: 0;
    list-style: none;
    font-family: "Arimo", Arial, sans-serif;
    font-size: 16px;
    line-height: 20.5px;
  }
  .contact-list b { font-weight: 700; }
  .address {
    position: absolute;
    top: 238px; left: 0; right: 0;
    font-family: "Open Sans", Arial, sans-serif;
    font-style: normal;
    font-size: 16px;
    line-height: 20px;
  }

  .brand-circle {
    position: absolute;
    left: 220px; top: 70px;
    width: 118px; height: 118px;
  }
  .brand-name {
    position: absolute;
    top: 222px; left: 0; right: 0;
    font-family: "Arimo", Arial, sans-serif;
    font-weight: 700;
    font-size: 40px;
    letter-spacing: 7px;
    line-height: 1;
    padding-left: 7px;
  }
</style>
</head>
<body>
<main class="canvas">
  <section class="card card--front">
    <h1 class="person-name">MARCUS ELLERY</h1>
    <p class="person-title">Managing Director</p>
    <div class="divider divider--upper"></div>
    <ul class="contact-list">
      <li><b>P:</b> 072-418 905 336</li>
      <li><b>M:</b> 072-418 905 336</li>
      <li><b>E:</b> info@skyvornq.com</li>
      <li><b>W:</b> www.skyvornq.com</li>
    </ul>
    <div class="divider divider--lower"></div>
    <address class="address">4827 Trellis Hollow Road<br>Fort Pierce, Florida, 34951</address>
  </section>

  <section class="card card--back">
    <svg class="brand-circle" viewBox="0 0 118 118" aria-hidden="true">
      <circle cx="59" cy="59" r="54" fill="none" stroke="var(--ink)" stroke-width="8"/>
    </svg>
    <p class="brand-name">SKYVORNQ</p>
  </section>
</main>
</body>
</html>
```